Carpet cleaning company focused on high quality needs business cards

We are a growing company that just merged with another company and need to design a new business card. We do both residential as well as commercial cleaning. We do carpet, tile & grout, upholstery, hard floors, and stain & pet odor removal. We treat our customers like family and strive to achieve outstanding results with every job.

```html
<!DOCTYPE html>
<html lang="en">
<head>
<meta charset="utf-8">
<title>Brightwell Steam Co. — Business Card</title>
<link rel="stylesheet" href="https://fonts.googleapis.com/css2?family=Montserrat:wght@400;500;700;800&display=swap">
<style>
  :root {
    --bg: #26272b;
    --card-red: #ec4b43;
    --card-white: #ffffff;
    --ink: #1f2226;
    --accent: #e8322e;
    --muted: #2c2f33;
  }
  * { box-sizing: border-box; margin: 0; padding: 0; }
  html, body { width: 1200px; height: 900px; overflow: hidden; }
  body {
    background: var(--bg);
    font-family: "Montserrat", Arial, sans-serif;
    display: flex;
    flex-direction: column;
    align-items: center;
    justify-content: center;
    gap: 56px;
  }
  .card {
    position: relative;
    width: 640px;
    height: 366px;
    border-radius: 26px;
    overflow: hidden;
  }
  .card--front {
    background: var(--card-red);
    display: flex;
    align-items: center;
    justify-content: center;
  }
  .brand {
    display: flex;
    align-items: center;
    gap: 16px;
  }
  .brand__square {
    width: 54px;
    height: 54px;
    flex: none;
  }
  .card--front .brand__square { background: var(--ink); }
  .card--back .brand__square { background: var(--accent); }
  .brand__name {
    font-weight: 800;
    font-size: 34px;
    line-height: 1.05;
    color: var(--ink);
    letter-spacing: -0.5px;
  }
  .card--back { background: var(--card-white); }
  .card--back .brand {
    position: absolute;
    top: 58px;
    right: 46px;
  }
  .card--back .brand__name { font-size: 30px; }
  .person {
    position: absolute;
    left: 48px;
    top: 150px;
  }
  .person__name {
    font-weight: 700;
    font-size: 27px;
    color: var(--accent);
  }
  .person__title {
    font-weight: 500;
    font-size: 14px;
    color: var(--muted);
    margin-top: 2px;
  }
  .address {
    position: absolute;
    left: 48px;
    top: 232px;
    font-size: 14px;
    line-height: 1.35;
    color: var(--muted);
  }
  .contacts {
    position: absolute;
    left: 48px;
    bottom: 26px;
    list-style: none;
    font-size: 13.5px;
    color: var(--muted);
  }
  .contacts li {
    display: flex;
    align-items: center;
    gap: 10px;
    height: 19px;
  }
  .contacts svg { width: 13px; height: 13px; flex: none; }
</style>
</head>
<body>
  <section class="card card--front" aria-label="Card front">
    <div class="brand">
      <span class="brand__square"></span>
      <span class="brand__name">Brightwell<br>Steam Co.</span>
    </div>
  </section>

  <section class="card card--back" aria-label="Card back">
    <div class="brand">
      <span class="brand__square"></span>
      <span class="brand__name">Brightwell<br>Steam Co.</span>
    </div>

    <div class="person">
      <p class="person__name">Daniel Reyes</p>
      <p class="person__title">CEO</p>
    </div>

    <p class="address">418 Maple Ridge Ave, #112<br>Fairview, OH 43210</p>

    <ul class="contacts">
      <li>
        <svg viewBox="0 0 16 16" aria-hidden="true"><path fill="#e8322e" d="M3 1h3l1.5 4-2 1.5a9 9 0 0 0 4 4L11 8.5l4 1.5v3a2 2 0 0 1-2 2A13 13 0 0 1 1 3a2 2 0 0 1 2-2z"/></svg>
        555 301-7724
      </li>
      <li>
        <svg viewBox="0 0 16 16" aria-hidden="true"><rect x="4" y="1" width="8" height="14" rx="1.5" fill="none" stroke="#e8322e" stroke-width="1.6"/><circle cx="8" cy="12.5" r="0.9" fill="#e8322e"/></svg>
        555 301-7724
      </li>
      <li>
        <svg viewBox="0 0 16 16" aria-hidden="true"><rect x="1" y="3" width="14" height="10" rx="1" fill="#e8322e"/><path d="M1.5 3.5 8 9l6.5-5.5" fill="none" stroke="#fff" stroke-width="1.3"/></svg>
        info@brightwellsteam.com
      </li>
      <li>
        <svg viewBox="0 0 16 16" aria-hidden="true"><circle cx="8" cy="8" r="6.5" fill="none" stroke="#e8322e" stroke-width="1.5"/><ellipse cx="8" cy="8" rx="2.8" ry="6.5" fill="none" stroke="#e8322e" stroke-width="1.2"/><path d="M1.5 8h13" stroke="#e8322e" stroke-width="1.2"/></svg>
        www.brightwellsteam.com
      </li>
    </ul>
  </section>
</body>
</html>
```